Seeking funky, innovative business cards

I am looking to refresh our current business cards to something more engaging, visual and impactful. We are a management consultancy firm, see website (www.larkstone-partners.com.au). I've included our colour scheme, sample of the slides we use and our old business cards. We would like our cards to have icons. The card should display:- Name- Title- Mobile number- Address- Email address- Website - Company logo- Our purpose statement "we shape workplaces people are proud to join"

Contact Information for Business Card

Brennan Ulfsson
Consultant
0468 927 341
Level 3, 218 Wexley Street, Melbourne 3000
brennan@larkstone-partners.com.au
www.larkstone-partners.com.au

Purpose statement "we shape workplaces people are proud to join"
LOGO available in google images

Font styles to use
Other font styles liked:
• Open Sans Light, Bebas Neue (open to other cool foints)

Colors
ffc214
5c5c5c
f5f5f5
fefefe

Requirements
Must have
• - Name
• - Title
• - Mobile number
• - Address
• - Email address
• - Website
• - Company logo
• - Our purpose statement "we shape workplaces people are proud to join"
Nice to have
• - Icons
• - Colour (see our colour scheme"

```html
<!DOCTYPE html>
<html lang="en">
<head>
<meta charset="utf-8">
<title>Larkstone Partners – Business Card</title>
<link rel="stylesheet" href="https://fonts.googleapis.com/css2?family=Open+Sans:wght@300;400;600;700&display=swap">
<style>
  :root {
    --brand-yellow: #ffc214;
    --brand-grey: #5c5c5c;
    --card-dark: #46494b;
    --paper: #fefefe;
    --backdrop: #e4e4e4;
    --text-dark: #3a3a3a;
  }
  * { box-sizing: border-box; margin: 0; padding: 0; }
  html, body {
    width: 1200px; height: 880px; overflow: hidden;
    background: var(--backdrop);
    font-family: "Open Sans", Arial, sans-serif;
  }
  .canvas {
    width: 1200px; height: 880px;
    display: flex; flex-direction: column;
    align-items: center; justify-content: center; gap: 48px;
  }
  .card {
    position: relative;
    width: 640px; height: 366px;
    border-radius: 22px;
    overflow: hidden;
    box-shadow: 0 10px 28px rgba(0,0,0,.18);
  }

  /* Back side */
  .card--back {
    background: var(--card-dark);
    display: flex; flex-direction: column;
    align-items: center; justify-content: center;
    color: #fff;
  }
  .wordmark {
    display: flex; align-items: center; gap: 14px;
    font-weight: 300; font-size: 46px; letter-spacing: .5px; line-height: 1.1;
  }
  .wordmark__dot {
    width: 16px; height: 16px; border-radius: 50%;
    background: var(--brand-yellow); flex: none;
  }
  .card--back .wordmark { color: #fff; }
  .purpose {
    margin-top: 18px;
    font-size: 17px; font-weight: 400; letter-spacing: .3px;
  }

  /* Front side */
  .card--front { background: var(--paper); }
  .card--front::after {
    content: ""; position: absolute; left: 0; right: 0; bottom: 0;
    height: 9px; background: var(--brand-yellow);
  }
  .card--front .wordmark {
    position: absolute; left: 44px; top: 66px;
    color: var(--brand-grey); font-size: 40px;
  }
  .person {
    position: absolute; left: 44px; right: 44px; top: 178px;
  }
  .person__row {
    display: flex; align-items: center; gap: 14px;
  }
  .person__name {
    font-weight: 700; font-size: 23px; line-height: 1.2;
    color: var(--text-dark); white-space: nowrap;
  }
  .divider {
    flex: 1; height: 1.5px; background: var(--brand-yellow);
    margin-top: 4px;
  }
  .person__title {
    font-weight: 400; font-size: 17px; line-height: 1.3;
    color: var(--brand-yellow);
  }
  .contacts {
    position: absolute; left: 44px; top: 248px;
    list-style: none; display: flex; flex-direction: column; gap: 8px;
  }
  .contacts__item {
    display: flex; align-items: center; gap: 10px;
    font-size: 16px; line-height: 1.3; color: var(--text-dark);
  }
  .contacts__icon {
    width: 20px; height: 20px; border-radius: 50%;
    background: var(--brand-yellow);
    display: flex; align-items: center; justify-content: center; flex: none;
  }
  .contacts__icon svg { width: 12px; height: 12px; }
  .address {
    position: absolute; right: 44px; top: 226px;
    font-style: normal; font-size: 16px; line-height: 1.4;
    color: var(--text-dark); text-align: right;
  }
</style>
</head>
<body>
<main class="canvas">
  <section class="card card--back" aria-label="Card back">
    <div class="wordmark"><span class="wordmark__dot"></span><span>Larkstone Partners</span></div>
    <p class="purpose">we shape workplaces people are proud to join</p>
  </section>

  <section class="card card--front" aria-label="Card front">
    <div class="wordmark"><span class="wordmark__dot"></span><span>Larkstone Partners</span></div>
    <div class="person">
      <div class="person__row">
        <p class="person__name">Brennan Ulfsson</p>
        <span class="divider"></span>
      </div>
      <p class="person__title">Consultant</p>
    </div>
    <ul class="contacts">
      <li class="contacts__item">
        <span class="contacts__icon">
          <svg viewBox="0 0 24 24" fill="#fff"><path d="M6.6 10.8a15.1 15.1 0 0 0 6.6 6.6l2.2-2.2a1 1 0 0 1 1-.25 11.4 11.4 0 0 0 3.6.57 1 1 0 0 1 1 1V20a1 1 0 0 1-1 1A17 17 0 0 1 3 4a1 1 0 0 1 1-1h3.5a1 1 0 0 1 1 1c0 1.25.2 2.45.57 3.57a1 1 0 0 1-.25 1z"/></svg>
        </span>0468 927 341
      </li>
      <li class="contacts__item">
        <span class="contacts__icon">
          <svg viewBox="0 0 24 24" fill="none" stroke="#fff" stroke-width="2.4"><rect x="3" y="5" width="18" height="14" rx="1.5"/><path d="M3 6l9 7 9-7"/></svg>
        </span>brennan@larkstone-partners.com.au
      </li>
      <li class="contacts__item">
        <span class="contacts__icon">
          <svg viewBox="0 0 24 24" fill="none" stroke="#fff" stroke-width="2.2"><circle cx="12" cy="12" r="9"/><path d="M3 12h18M12 3c3 3 3 15 0 18M12 3c-3 3-3 15 0 18"/></svg>
        </span>www.larkstone-partners.com.au
      </li>
    </ul>
    <address class="address">Level 3, 218 Wexley Street<br>Melbourne 3000</address>
  </section>
</main>
</body>
</html>
```